New Company Logo & Responsive Website Design for Codeworks Heron

Codeworks Heron provides a white labeled, digital lending platform technology solutions to the mortgage industry via a SaaS model. Our target market is Mortgage Companies and Banks who are looking for innovative technology to assist both borrowers and loan originators with the lending process, while automating as much of he process as possible.

Codeworks Heron is our company name, and our modular software offerings Include the following Products:

1) Applicant Heron: A customizable, web based, point-of-sale application for borrowers to complete a loan application, and guide them through the mortgage process.

POS Definition
"A point of sale (POS) is the client-facing software solution that allows borrowers to create a customer portal, apply for a loan online, and seamlessly submit needed documentation."

2) Ledger Heron: A Mortgage Loan Origination System

LOS Definition
"A Mortgage Loan Origination System (LOS) is a platform that takes a completed loan application and facilitates the mortgage transaction from origination to post closing. LOS systems may include document management, pricing and eligibility engines, and compliance tools to decrease risk and increase loan manufacturing quality.

3) Dwelling Heron: A brandable, home search website

The LOS and POS definitions provided above are just for your understanding of what these products are, not to be included word-for-word as website content.

We are looking for designs that are elegant, convey technical competency, simple to navigate, and set us apart from the competition.

We are not set on any particular colors at this point, so feel free to choose the best colors for your particular designs.

Please include company logo, both desktop and mobile designs with a template design for the website sub pages.

Some Examples of Mortgage Technology Websites offering similar products. These are to show the typical content, not designs that we particularly like or dislike.

https://brantiq.example/
https://www.clearvantro.example/
https://www.abodefundbuddy.example/
https://www.debtquokka.example/
https://www.ternixapps.example/products/trail

Please send comments with additional questions.

Thank You For your participation.

Mortgage Companies

```html
<!DOCTYPE html>
<html lang="en">
<head>
<meta charset="utf-8">
<title>Codeworks Heron</title>
<link href="https://fonts.googleapis.com/css2?family=Michroma&family=Montserrat:ital,wght@0,400;0,500;0,600;0,700;1,400&display=swap" rel="stylesheet">
<style>
:root{
  --red:#e0091c;
  --navy:#0b2a87;
  --ink:#222;
  --muted:#666;
  --grey-bg:#f0f0f0;
  --footer:#0d1a3e;
  --white:#fff;
}
*{box-sizing:border-box;margin:0;padding:0}
html,body{width:1200px;height:3587px;overflow:hidden}
body{position:relative;font-family:'Montserrat',sans-serif;color:var(--ink);background:var(--white)}
.abs{position:absolute}
.display{font-family:'Michroma',sans-serif}

/* header */
.header{left:0;top:0;width:1200px;height:82px;background:var(--white)}
.brand{left:111px;top:20px;font-size:29px;font-weight:700;color:#333;white-space:nowrap;z-index:2}
.nav{top:30px;font-size:15px;color:#333;white-space:nowrap;z-index:2}
.nav.active{color:#e84a2a}
.call-btn{left:897px;top:15px;width:189px;height:53px;background:var(--navy);border-radius:6px;color:var(--white);font-size:16px;font-weight:700;display:flex;align-items:center;justify-content:center;gap:9px;white-space:nowrap;z-index:2}

/* hero */
.hero{left:0;top:82px;width:1200px;height:670px}
.hero-box{left:230px;top:261px;width:739px;height:259px;background:rgba(40,40,40,.62)}
.hero-title{left:230px;top:290px;width:739px;text-align:center;color:var(--white);font-size:38px;letter-spacing:3px;white-space:nowrap}
.hero-text{left:300px;top:344px;width:600px;text-align:center;color:var(--white);font-size:15.5px;line-height:31px}
.hero-btn{left:506px;top:423px;width:188px;height:55px;background:var(--red);border-radius:6px;color:var(--white);font-weight:700;font-size:17px;display:flex;align-items:center;justify-content:center}
.dot{top:666px;width:13px;height:13px;border:1.5px solid var(--white)}
.dot.on{background:var(--white)}
.follow{left:1142px;top:244px;writing-mode:vertical-rl;color:var(--white);font-size:8px;letter-spacing:4px}
.hero-social{left:1135px;width:34px;height:34px;border:1.5px solid var(--white);border-radius:50%}

/* section headings */
.h-sec{font-size:32px;letter-spacing:7px;color:#111;white-space:nowrap}
.bar{height:3px;background:var(--red)}

/* about */
.about-block{left:63px;top:781px;width:367px;height:387px;background:var(--red)}
.about-frame{left:95px;top:805px;width:176px;height:170px;border:2px solid var(--white);border-right:none;border-bottom:none}
.p{font-size:14px;line-height:26.6px;color:var(--muted);text-align:justify}

/* offerings */
.offer-bg{left:0;top:1359px;width:1200px;height:645px;background:var(--grey-bg)}
.offer-title{left:0;top:1421px;width:1200px;text-align:center;font-size:25px;letter-spacing:6px;color:#111;white-space:nowrap}
.offer-lead{left:220px;top:1493px;width:760px;text-align:center;font-size:16px;line-height:28px;color:#444}
.card-img{top:1574px;width:318px;height:256px;box-shadow:0 3px 6px rgba(0,0,0,.18)}
.card-name{top:1841px;font-size:15.5px;font-weight:700;color:#222}
.card-desc{top:1874px;width:300px;font-size:12.5px;line-height:24px;color:#555}

/* testimonials */
.testi-title{left:0;top:2068px;width:1200px;text-align:center;font-size:40px;color:#222;letter-spacing:1px;white-space:nowrap}
.testi-card{top:2185px;width:301px;height:350px;background:var(--white);border-radius:10px;box-shadow:0 0 10px rgba(0,0,0,.16)}
.testi-text{position:absolute;left:21px;top:28px;width:262px;font-size:13.3px;line-height:28.2px;font-style:italic;color:#777}
.testi-name{position:absolute;left:25px;top:288px;font-size:16px;color:var(--red)}
.testi-role{position:absolute;left:25px;top:313px;font-size:11px;color:#777}
.testi-quote{position:absolute;left:236px;top:292px}
.arrow{top:2335px;width:34px;height:34px;border:1.5px solid #222;border-radius:50%}

/* contact */
.field{border:1px solid #bdbdbd;background:var(--white);font-size:14px;color:#777;padding:0 10px;display:flex;align-items:center}
.send{left:111px;top:2974px;width:532px;height:57px;background:var(--navy);color:var(--white);font-weight:700;font-size:18px;display:flex;align-items:center;justify-content:center;box-shadow:0 3px 5px rgba(0,0,0,.2)}
.c-icon{width:52px;height:52px;border-radius:50%;background:var(--red);display:flex;align-items:center;justify-content:center}
.c-label{font-size:16px;font-weight:500;color:#222}
.c-text{font-size:15px;line-height:26px;color:#555}

/* footer */
.footer{left:0;top:3088px;width:1200px;height:499px}
.f-head{top:3213px;font-size:16px;letter-spacing:3px;color:var(--white);white-space:nowrap}
.f-bar{top:3246px;width:30px;height:2px;background:var(--white)}
.f-list{top:3259px;list-style:none;font-size:14.5px;line-height:33.5px;color:var(--white)}
.f-news{left:813px;top:3260px;width:290px;font-size:13.5px;line-height:23px;color:var(--white)}
.f-input{left:809px;top:3331px;width:277px;height:42px;background:var(--white);border-radius:21px;font-size:12px;color:#222;padding-left:20px;display:flex;align-items:center}
.f-send{left:1049px;top:3343px;width:18px;height:18px;border-radius:50%;background:var(--red)}
.f-social{top:3403px;width:48px;height:48px;border:1.5px solid var(--white);border-radius:50%}
.f-rule{left:111px;top:3488px;width:977px;height:1px;background:rgba(255,255,255,.6)}
.f-small{top:3527px;font-size:13px;color:var(--white)}
</style>
</head>
<body>

<!-- header -->
<div class="abs header"></div>
<div class="abs brand">Codeworks Heron</div>
<div class="abs nav active" style="left:509px">Home</div>
<div class="abs nav" style="left:581px">About Us</div>
<div class="abs nav" style="left:675px">Services</div>
<div class="abs nav" style="left:762px">Blog</div>
<div class="abs nav" style="left:822px">Contact</div>
<div class="abs call-btn">
  <svg width="16" height="16" viewBox="0 0 24 24"><path fill="#fff" d="M6.6 10.8a15.1 15.1 0 0 0 6.6 6.6l2.2-2.2c.3-.3.7-.4 1-.2 1.1.4 2.3.6 3.6.6.6 0 1 .4 1 1V20c0 .6-.4 1-1 1A17 17 0 0 1 3 4c0-.6.4-1 1-1h3.5c.6 0 1 .4 1 1 0 1.3.2 2.5.6 3.6.1.3 0 .7-.2 1z"/></svg>
  +1 555 010 0199
</div>

<!-- hero -->
<svg class="abs hero" viewBox="0 0 1200 670" role="img" aria-label="Photo of three colleagues smiling around a tablet in a bright office">
  <defs><linearGradient id="heroG" x1="0" y1="0" x2="1" y2="1">
    <stop offset="0" stop-color="#c9b8a3"/><stop offset=".45" stop-color="#6f7c8d"/><stop offset="1" stop-color="#8e8a86"/></linearGradient></defs>
  <polygon points="0,0 1200,0 1200,668 0,618" fill="url(#heroG)"/>
</svg>
<div class="abs hero-box"></div>
<div class="abs display hero-title">CODEWORKS HERON</div>
<div class="abs hero-text">Lorem ipsum dolor sit amet, consectetur adipiscing elit, sed do eiusmod tempor incididunt ut labore et dolore magna aliqua.</div>
<div class="abs hero-btn">GET STARTED</div>
<div class="abs dot" style="left:557px"></div>
<div class="abs dot" style="left:575px"></div>
<div class="abs dot on" style="left:593px"></div>
<div class="abs dot" style="left:611px"></div>
<div class="abs dot" style="left:629px"></div>
<div class="abs follow">FOLLOW US</div>
<div class="abs hero-social" style="top:418px" aria-label="Social profile"></div>
<div class="abs hero-social" style="top:461px" aria-label="Social profile"></div>
<div class="abs hero-social" style="top:503px" aria-label="Social profile"></div>

<!-- about -->
<div class="abs about-block"></div>
<div class="abs about-frame"></div>
<div class="abs" role="img" aria-label="Photo of two businessmen smiling at a laptop" style="left:111px;top:818px;width:367px;height:387px;background:linear-gradient(135deg,#e9e4dc,#9a958f 60%,#cfc8bf)"></div>
<div class="abs" role="img" aria-label="Illustration of a hand touching a glowing network of technology icons" style="left:254px;top:1012px;width:315px;height:270px;background:radial-gradient(circle at 50% 45%,#d79a5a,#3c6f8c 45%,#1f3d52)"></div>
<div class="abs display h-sec" style="left:600px;top:850px">ABOUT US</div>
<div class="abs bar" style="left:600px;top:904px;width:83px"></div>
<p class="abs p" style="left:600px;top:930px;width:486px">Lorem ipsum dolor sit amet, consectetur adipiscing elit, sed do eiusmod tempor incididunt ut labore et dolore magna aliqua. Ut enim ad minim veniam, quis nostrud exercitation ullamco laboris nisi ut aliquip ex ea commodo consequat. Duis aute irure dolor in reprehenderit in voluptate velit esse cillum dolore eu fugiat nulla pariatur. Excepteur sint occaecat cupidatat</p>
<p class="abs p" style="left:600px;top:1110px;width:486px">Lorem ipsum dolor sit amet, consectetur adipiscing elit, sed do eiusmod tempor incididunt ut labore et dolore magna aliqua. Ut enim ad minim veniam, quis nostrud exercitation ullamco laboris nisi ut aliquip ex ea commodo consequat. Duis aute irure dolor in reprehenderit in voluptate velit esse cillum</p>

<!-- offerings -->
<div class="abs offer-bg"></div>
<div class="abs display offer-title">OUR MODULAR SOFTWARE OFFERINGS</div>
<div class="abs bar" style="left:558px;top:1470px;width:84px"></div>
<div class="abs offer-lead">Lorem ipsum dolor sit amet, consectetur adipiscing elit, sed do eiusmod tempor incididunt ut labore et dolore magna aliqua. Ut enim ad minim veniam,</div>
<div class="abs card-img" role="img" aria-label="Photo of hands at a laptop with holographic data graphics" style="left:111px;background:linear-gradient(135deg,#1d3a47,#4fa4a8 50%,#2c3036)"></div>
<div class="abs card-img" role="img" aria-label="Photo of a team meeting around a laptop in an office" style="left:442px;background:linear-gradient(135deg,#b8b4ad,#5e6a7a 55%,#d8d2c8)"></div>
<div class="abs card-img" role="img" aria-label="Photo of a laptop with floating real estate icons" style="left:771px;background:linear-gradient(135deg,#6c6660,#c7c2bc 50%,#3f3b38)"></div>
<div class="abs card-name" style="left:110px">Applicant Heron</div>
<div class="abs card-name" style="left:440px">Ledger Heron</div>
<div class="abs card-name" style="left:769px">Dwelling Heron:</div>
<div class="abs card-desc" style="left:111px">A customizable, web based, point-of-sale application for borrowers to complete a loan application, and guide them through the mortgage process.</div>
<div class="abs card-desc" style="left:441px">A Mortgage Loan Origination System</div>
<div class="abs card-desc" style="left:771px">A brandable, home search website</div>

<!-- testimonials -->
<div class="abs display testi-title">CUSTOMER TESTIMONIALS</div>
<div class="abs" style="left:545px;top:2132px;width:109px;height:5px;background:var(--navy)"></div>
<div class="abs arrow" style="left:63px"><svg width="31" height="31" viewBox="0 0 31 31"><path d="M18 9l-6 6.5 6 6.5" fill="none" stroke="#222" stroke-width="2"/></svg></div>
<div class="abs arrow" style="left:1098px"><svg width="31" height="31" viewBox="0 0 31 31"><path d="M13 9l6 6.5-6 6.5" fill="none" stroke="#222" stroke-width="2"/></svg></div>

<div class="abs testi-card" style="left:127px">
  <p class="testi-text">Lorem ipsum dolor sit consectetur adipiscing elit, sed do eiusmod tempor incididunt ut labore et dolore magna aliqua. Ut enim ad minim veniam, quis nostrud exercitation ullamco laboris nisi ut aliquip ex ea consequat. Duis aute irure dolor in reprehenderit in voluptate velit esse</p>
  <div class="testi-name">Mara Quillfeather</div>
  <div class="testi-role">Lorem ipsum dolor sit</div>
  <svg class="testi-quote" width="42" height="34" viewBox="0 0 42 34"><path fill="#0b2a87" d="M0 34V18C0 8 5 2 15 0l2 5c-5 2-7 5-7 10h8v19zM24 34V18c0-10 5-16 15-18l2 5c-5 2-7 5-7 10h8v19z"/></svg>
</div>
<div class="abs testi-card" style="left:449px">
  <p class="testi-text">Lorem ipsum dolor sit consectetur adipiscing elit, sed do eiusmod tempor incididunt ut labore et dolore magna aliqua. Ut enim ad minim veniam, quis nostrud exercitation ullamco laboris nisi ut aliquip ex ea consequat. Duis aute irure dolor in reprehenderit in voluptate velit esse</p>
  <div class="testi-name">Mara Quillfeather</div>
  <div class="testi-role">Lorem ipsum dolor sit</div>
  <svg class="testi-quote" width="42" height="34" viewBox="0 0 42 34"><path fill="#0b2a87" d="M0 34V18C0 8 5 2 15 0l2 5c-5 2-7 5-7 10h8v19zM24 34V18c0-10 5-16 15-18l2 5c-5 2-7 5-7 10h8v19z"/></svg>
</div>
<div class="abs testi-card" style="left:771px">
  <p class="testi-text">Lorem ipsum dolor sit consectetur adipiscing elit, sed do eiusmod tempor incididunt ut labore et dolore magna aliqua. Ut enim ad minim veniam, quis nostrud exercitation ullamco laboris nisi ut aliquip ex ea consequat. Duis aute irure dolor in reprehenderit in voluptate velit esse</p>
  <div class="testi-name">Mara Quillfeather</div>
  <div class="testi-role">Lorem ipsum dolor sit</div>
  <svg class="testi-quote" width="42" height="34" viewBox="0 0 42 34"><path fill="#0b2a87" d="M0 34V18C0 8 5 2 15 0l2 5c-5 2-7 5-7 10h8v19zM24 34V18c0-10 5-16 15-18l2 5c-5 2-7 5-7 10h8v19z"/></svg>
</div>

<!-- contact -->
<div class="abs field" style="left:111px;top:2698px;width:260px;height:55px">First Name</div>
<div class="abs field" style="left:383px;top:2698px;width:260px;height:55px">Last Name</div>
<div class="abs field" style="left:111px;top:2768px;width:260px;height:55px">Email</div>
<div class="abs field" style="left:383px;top:2768px;width:260px;height:55px">Phone Number</div>
<div class="abs field" style="left:111px;top:2841px;width:532px;height:116px;align-items:flex-start;padding-top:18px">Message</div>
<div class="abs send">SEND US MESSAGE</div>

<div class="abs display h-sec" style="left:680px;top:2695px">CONTACT US</div>
<div class="abs bar" style="left:680px;top:2749px;width:89px"></div>

<div class="abs c-icon" style="left:677px;top:2788px"><svg width="20" height="24" viewBox="0 0 20 24"><path fill="#fff" d="M10 0a9 9 0 0 0-9 9c0 7 9 15 9 15s9-8 9-15a9 9 0 0 0-9-9zm0 12.5A3.5 3.5 0 1 1 10 5.5a3.5 3.5 0 0 1 0 7z"/></svg></div>
<div class="abs c-label" style="left:750px;top:2789px">ADDRESS</div>
<div class="abs c-text" style="left:750px;top:2813px;width:320px">Lorem ipsum dolor sit amet, consectetur adipiscing elit, sed do eiusmod</div>

<div class="abs c-icon" style="left:677px;top:2884px"><svg width="22" height="22" viewBox="0 0 24 24"><path fill="#fff" d="M6.6 10.8a15.1 15.1 0 0 0 6.6 6.6l2.2-2.2c.3-.3.7-.4 1-.2 1.1.4 2.3.6 3.6.6.6 0 1 .4 1 1V20c0 .6-.4 1-1 1A17 17 0 0 1 3 4c0-.6.4-1 1-1h3.5c.6 0 1 .4 1 1 0 1.3.2 2.5.6 3.6.1.3 0 .7-.2 1z"/></svg></div>
<div class="abs c-label" style="left:750px;top:2887px">CALL NOW</div>
<div class="abs c-text" style="left:750px;top:2911px;font-weight:500">+1 555 010 0199</div>

<div class="abs c-icon" style="left:677px;top:2967px"><svg width="24" height="18" viewBox="0 0 24 18"><rect width="24" height="18" rx="2" fill="#fff"/><path d="M1 2l11 8 11-8" fill="none" stroke="#e0091c" stroke-width="2"/></svg></div>
<div class="abs c-label" style="left:750px;top:2970px">EMAIL</div>
<div class="abs c-text" style="left:750px;top:2994px">info@CodeworksHeron.com</div>

<!-- footer -->
<svg class="abs footer" viewBox="0 0 1200 499" preserveAspectRatio="none" aria-hidden="true">
  <defs><linearGradient id="footG" x1="0" y1="0" x2="1" y2="1">
    <stop offset="0" stop-color="#0d1a3e"/><stop offset=".5" stop-color="#15265a"/><stop offset="1" stop-color="#0b1533"/></linearGradient></defs>
  <polygon points="0,0 1200,60 1200,499 0,499" fill="url(#footG)"/>
</svg>
<div class="abs display f-head" style="left:111px">QUICK LINKS</div>
<div class="abs display f-head" style="left:335px">SERVICES</div>
<div class="abs display f-head" style="left:544px">SUPPORT</div>
<div class="abs display f-head" style="left:813px">NEWSLETTER</div>
<div class="abs f-bar" style="left:111px"></div>
<div class="abs f-bar" style="left:335px"></div>
<div class="abs f-bar" style="left:544px"></div>
<div class="abs f-bar" style="left:813px"></div>
<ul class="abs f-list" style="left:111px"><li>Home</li><li>About Us</li><li>Services</li><li>Blog</li><li>Contact Us</li></ul>
<ul class="abs f-list" style="left:335px"><li>Applicant Heron</li><li>Ledger Heron</li><li>&nbsp;Dwelling Heron</li></ul>
<ul class="abs f-list" style="left:544px"><li>Help</li><li>General Inforamtion</li><li>Legal Policy</li><li>Disclaimer</li></ul>
<div class="abs f-news">Lorem ipsum dolor sit amet, consectetur adipiscing elit, sed do eiusmod tempor</div>
<div class="abs f-input">Enter Email</div>
<div class="abs f-send"><svg width="18" height="18" viewBox="0 0 18 18"><path fill="#fff" d="M4 9l9-4-3 9-1.5-3.5z"/></svg></div>
<div class="abs f-social" style="left:816px" aria-label="Social profile"></div>
<div class="abs f-social" style="left:873px" aria-label="Social profile"></div>
<div class="abs f-social" style="left:930px" aria-label="Social profile"></div>
<div class="abs f-rule"></div>
<div class="abs f-small" style="left:112px">© 2022 CODEWORKS HERON All Rights Reserved</div>
<div class="abs f-small" style="left:914px">Terms of use | Privacy Policy</div>

</body>
</html>
```